Webdesign für Branchenverzeichnis
Zielgruppe
Wir-bauen-Brücken – das Branchenverzeichnis der Selbstverantwortlichen.
Der Anbieter präsentiert sich mit seinem Namen und der URL - ähnlich wie bei 'blaue Tafeln' oder Jobkranich.
Aufgabenstellung
Das Branchenverzeichnis sollte neutral und gleichzeitig hochwertig sein. Die Hauptfarben sind Gold, Schwarz und Weiß. Logo und Corporate Design wurden bereits entwickelt

```html
<!DOCTYPE html>
<html lang="de">
<head>
<meta charset="utf-8">
<title>Jonas Beispiel Firma – Wir-bauen-Brücken</title>
<link href="https://fonts.googleapis.com/css2?family=Montserrat:wght@400;500;600;700&family=Quicksand:wght@400;500&display=swap" rel="stylesheet">
<style>
:root{
  --gold:#d4b062;
  --gold-pale:#efe3c4;
  --line:#e6d6ad;
  --dark:#3a3a3a;
  --black:#111;
  --text:#7a7a7a;
  --white:#fff;
}
*{box-sizing:border-box;margin:0;padding:0}
html,body{width:801px;height:1200px;overflow:hidden;background:var(--white)}
body{position:relative;font-family:'Quicksand',sans-serif;color:var(--text)}
.abs{position:absolute}
/* header */
.site-header{left:0;top:0;width:801px;height:42px;background:var(--dark)}
.brand{left:105px;top:13px;display:flex;align-items:center;gap:4px;color:var(--gold);font-family:'Montserrat',sans-serif;font-weight:600;font-size:6.5px}
.brand-dot{width:14px;height:14px;border:1.5px solid var(--gold);border-radius:50%}
.main-nav a{position:absolute;top:17px;font-family:'Montserrat',sans-serif;font-weight:500;font-size:6.3px;letter-spacing:.6px;color:var(--white);text-decoration:none}
.main-nav a.active{color:var(--gold)}
.header-icons{left:549px;top:16px;display:flex;gap:5px;align-items:center}
.btn-member{left:613px;top:11px;width:84px;height:19px;background:var(--gold);color:var(--white);font-family:'Montserrat',sans-serif;font-size:5.6px;letter-spacing:.4px;display:flex;align-items:center;justify-content:center}
/* hero */
.hero-photo{top:42px;height:164px;width:200px}
/* title band */
.title-band{left:0;top:206px;width:801px;height:105px;background:var(--gold)}
.company-title{left:105px;top:239px;font-family:'Montserrat',sans-serif;font-weight:600;font-size:18.5px;letter-spacing:1.2px;color:var(--white)}
.company-meta{left:106px;top:267px;display:flex;gap:13px;font-family:'Montserrat',sans-serif;font-size:6.3px;letter-spacing:.4px;color:var(--white)}
.company-meta span{display:flex;align-items:center;gap:3px}
.btn-dark{left:622px;width:75px;height:12.5px;background:var(--black);color:var(--white);font-size:6px;display:flex;align-items:center;justify-content:center}
/* content */
.section-title{left:109px;font-family:'Montserrat',sans-serif;font-size:10.5px;color:#444;letter-spacing:.5px}
.section-rule{left:104px;width:386px;height:1px;background:var(--line)}
.profile-text{left:109px;top:364px;width:381px;font-size:6.3px;line-height:11.7px;letter-spacing:.2px}
.faq-item{left:109px;width:381px;height:25px;border:1px solid var(--line);display:flex;align-items:center;justify-content:space-between;padding:0 8px 0 9px;font-size:6.4px;color:#666}
.review-card{left:104px;top:781px;width:382px;height:121px;border:1px solid var(--line);border-radius:20px}
.avatar{left:122px;top:793px;width:56px;height:56px;border-radius:50%;background:radial-gradient(circle at 50% 45%,#ddd0c2,#a89a8c)}
.reviewer{left:104px;top:855px;width:92px;text-align:center;font-family:'Montserrat',sans-serif;color:#222}
.reviewer b{display:block;font-weight:600;font-size:7.5px;letter-spacing:.6px}
.reviewer small{display:block;font-size:5.8px;letter-spacing:.4px;margin-top:3px}
.review-text{left:223px;top:797px;width:245px;font-size:6.3px;line-height:13px;letter-spacing:.2px}
.quote-mark{left:308px;top:850px;font-family:'Montserrat',sans-serif;font-weight:700;font-size:56px;line-height:1;color:var(--gold-pale)}
/* sidebar */
.side-box{left:518px;width:179px;border:1px solid var(--line)}
.side-head{position:absolute;left:-1px;top:-1px;width:179px;height:25px;background:var(--gold);color:var(--white);font-family:'Montserrat',sans-serif;font-size:9px;letter-spacing:.4px;display:flex;align-items:center;justify-content:space-between;padding:0 9px}
.map{left:518px;top:383px;width:179px;height:80px;background:linear-gradient(90deg,#e2e0dc 0%,#eeece8 45%,#e8e1d8 60%,#f1efeb 100%)}
.data-row{left:518px;width:179px;height:25px;border:1px solid var(--line);border-top:none;display:flex;align-items:center;gap:10px;padding-left:7px;font-size:6.2px;color:#777}
.hours-row{left:518px;width:179px;height:24.5px;border:1px solid var(--line);border-top:none;display:flex;align-items:center;padding-left:9px;font-size:6px;color:#888}
.hours-row span:first-child{width:34px}
.field{left:528px;width:154px;border:1px solid #ddd;display:flex;align-items:center;justify-content:space-between;padding:0 9px;font-size:5.6px;color:#aaa}
.btn-send{left:528px;top:935px;width:154px;height:24px;background:var(--gold);color:var(--white);font-size:6.5px;display:flex;align-items:center;justify-content:center;box-shadow:0 2px 4px rgba(0,0,0,.12)}
/* footer */
.site-footer{left:0;top:1020px;width:801px;height:180px;background:var(--dark);color:#ddd}
.footer-brand{left:171px;top:1070px;width:44px;text-align:center;color:var(--white);font-family:'Montserrat',sans-serif;font-size:5px;font-weight:600}
.footer-brand .ring{width:30px;height:30px;border:1.5px solid var(--white);border-radius:50%;margin:0 auto 3px}
.footer-title{top:1072px;font-family:'Montserrat',sans-serif;font-weight:600;font-size:7.5px;letter-spacing:.4px;color:var(--white)}
.footer-about{left:240px;top:1091px;width:125px;font-size:6.2px;line-height:10.5px;color:#ddd}
.footer-about a{color:var(--gold);display:block;margin-top:3px}
.footer-links{top:1091px;font-size:6.3px;line-height:16.7px;color:#ddd;list-style:none}
.copyright{left:0;top:1181px;width:801px;text-align:center;font-family:'Montserrat',sans-serif;font-size:5px;color:#ddd}
</style>
</head>
<body>

<header class="abs site-header">
  <div class="abs brand"><span class="brand-dot"></span>Wir-bauen-Brücken</div>
  <nav class="main-nav">
    <a style="left:192px">HOME</a>
    <a class="active" style="left:242px">SUCHEN</a>
    <a style="left:300px">ÜBER UNS</a>
    <a style="left:363px">MITGLIEDSCHAFT</a>
    <a style="left:451px">KONTAKT</a>
  </nav>
  <div class="abs header-icons">
    <svg width="8" height="8"><rect x="0.5" y="0.5" width="7" height="7" rx="2" fill="none" stroke="#fff"/></svg>
    <svg width="8" height="8"><rect width="8" height="8" fill="#fff"/></svg>
    <svg width="9" height="9" viewBox="0 0 9 9"><circle cx="4.5" cy="2.5" r="2.3" fill="#fff"/><path d="M0.5 9c0-3 1.8-4 4-4s4 1 4 4z" fill="#fff"/></svg>
  </div>
  <div class="abs btn-member">MITGLIED WERDEN</div>
</header>

<div class="abs hero-photo" style="left:0;background:linear-gradient(135deg,#8d7a62,#c9b89b 60%,#6d5c4a)" role="img" aria-label="Foto: Hände mit Laptop, Tablet und Diagrammen auf einem Holztisch"></div>
<div class="abs hero-photo" style="left:200px;background:linear-gradient(135deg,#d9d6d2,#f3f1ee 50%,#8a7d6e)" role="img" aria-label="Foto: Zwei Personen präsentieren vor einem Whiteboard"></div>
<div class="abs hero-photo" style="left:400px;background:linear-gradient(135deg,#5b4d40,#a58d72 55%,#3c3833)" role="img" aria-label="Foto: Team bespricht Unterlagen im Büro"></div>
<div class="abs hero-photo" style="left:601px;width:200px;background:linear-gradient(135deg,#39414e,#9ea8b3 55%,#d8d6d2)" role="img" aria-label="Foto: Kollegen vor Monitoren mit Datenanalysen"></div>

<section class="abs title-band"></section>
<h1 class="abs company-title">Jonas Beispiel Firma IT &amp; Online</h1>
<div class="abs company-meta">
  <span><svg width="8" height="8" viewBox="0 0 8 8"><rect x="0.6" y="1.2" width="6.8" height="6.2" fill="none" stroke="#fff"/><rect x="2" y="3.5" width="2" height="2" fill="#fff"/></svg>IT &amp; Marketing</span>
  <span><svg width="6" height="8" viewBox="0 0 6 8"><path d="M3 0a3 3 0 0 1 3 3c0 2-3 5-3 5S0 5 0 3a3 3 0 0 1 3-3z" fill="#fff"/><circle cx="3" cy="3" r="1" fill="#d4b062"/></svg>München</span>
</div>
<div class="abs btn-dark" style="top:247px">Firmenbeitrag teilen</div>
<div class="abs btn-dark" style="top:266px">Rezension schreiben</div>

<h2 class="abs section-title" style="top:341px">Firmenprofil</h2>
<div class="abs section-rule" style="top:358px"></div>
<p class="abs profile-text">Lorem ipsum dolor sit amet, consectetur adipisicing elit, sed do eiusmod tempor incididunt ut labore et dolore. magna aliqua. Duis aute irure dolor in reprehenderit in voluptate velit esse cillum dolore eu fugiat nulla pariatur. Ut enim ad minim veniam, quis nostrud exercitation ullamco laboris nisi ut aliquip ex ea commodo!Lorem ipsum dolor sit amet, consectetur adipisicing elit, sed do eiusmod tempor incididunt ut labore et dolore. magna aliqua. Duis aute irure dolor in reprehenderit in voluptate velit esse cillum dolore eu fugiat nulla pariatur. Ut enim ad minim veniam, quis nostrud exercitation ullamco laboris nisi ut aliquip ex ea commodo!Lorem ipsum dolor sit amet, consectetur adipisicing elit, sed do eiusmod tempor incididunt ut labore et dolore. magna aliqua. Duis aute irure dolor in reprehenderit in voluptate velit esse cillum dolore eu fugiat nulla pariatur. Ut enim ad minim veniam, quis nostrud exercitation ullamco laboris nisi ut aliquip ex ea commodo!Lorem ipsum dolor sit amet, consectetur adipisicing elit, sed do eiusmod tempor incididunt ut labore et dolore. magna aliqua. Duis aute irure dolor in reprehenderit in voluptate velit esse cillum dolore eu fugiat nulla pariatur. Ut enim ad minim veniam, quis nostrud exercitation ullamco laboris nisi ut aliquip ex ea commodo!Lorem ipsum dolor sit amet, consectetur adipisicing elit, sed do eiusmod tempor incididunt ut labore et dolore. magna aliqua. Duis</p>

<div class="abs faq-item" style="top:538px">Wie können Sie uns am schnellsten kontaktieren?<svg width="8" height="5" viewBox="0 0 8 5"><path d="M0.5 0.5L4 4 7.5 0.5" fill="none" stroke="#d4b062" stroke-width="1.2"/></svg></div>
<div class="abs faq-item" style="top:570px">Wie können Sie uns am schnellsten kontaktieren?<svg width="8" height="5" viewBox="0 0 8 5"><path d="M0.5 0.5L4 4 7.5 0.5" fill="none" stroke="#d4b062" stroke-width="1.2"/></svg></div>
<div class="abs faq-item" style="top:601px">Spezialisierung für individuelle Lösungen bei Content Management Systemen<svg width="8" height="5" viewBox="0 0 8 5"><path d="M0.5 0.5L4 4 7.5 0.5" fill="none" stroke="#d4b062" stroke-width="1.2"/></svg></div>
<div class="abs faq-item" style="top:632px">Wie können Sie uns am schnellsten kontaktieren?<svg width="8" height="5" viewBox="0 0 8 5"><path d="M0.5 0.5L4 4 7.5 0.5" fill="none" stroke="#d4b062" stroke-width="1.2"/></svg></div>
<div class="abs faq-item" style="top:664px">Spezialisierung für individuelle Lösungen bei Content Management Systemen<svg width="8" height="5" viewBox="0 0 8 5"><path d="M0.5 0.5L4 4 7.5 0.5" fill="none" stroke="#d4b062" stroke-width="1.2"/></svg></div>

<h2 class="abs section-title" style="top:745px">Rezensionen</h2>
<div class="abs section-rule" style="top:762px"></div>
<div class="abs review-card"></div>
<div class="abs avatar" role="img" aria-label="Porträtfoto der Rezensentin"></div>
<div class="abs reviewer"><b>Clara Lindner</b><small>Buchhaltung, 54 Jahre</small></div>
<div class="abs quote-mark">”</div>
<p class="abs review-text">Lorem ipsum dolor sit amet, consectetuer adipiscing elit. Aenean commodo ligula eget dolor. Aenean massa. Cum sociis natoque penatibus et magnis dis parturient montes, nascetur ridiculus mus. Donec quam felis, ultricies nec, pellentesque eu, pretium quis, sem. Nulla consequat massa quis enim. Donec pede justo, fringilla vel, aliquet nec, vulputate eget, arcu. In enim justo, rhoncus ut, imperdiet a, venenatis vitae, justo. Nullam dictum felis eu pede</p>

<!-- sidebar: Firmendaten -->
<div class="abs side-box" style="top:358px;height:181px">
  <div class="side-head">Firmendaten<svg width="11" height="11" viewBox="0 0 11 11"><circle cx="5.5" cy="5.5" r="5.5" fill="#fff"/><circle cx="5.5" cy="4.2" r="1.8" fill="#d4b062"/><path d="M2.5 9c.6-1.6 1.7-2.3 3-2.3s2.4.7 3 2.3z" fill="#d4b062"/></svg></div>
</div>
<div class="abs map" role="img" aria-label="Karte mit Standortmarkierung"></div>
<div class="abs data-row" style="top:463px;border-top:1px solid var(--line)"><svg width="6" height="8" viewBox="0 0 6 8"><path d="M3 0a3 3 0 0 1 3 3c0 2-3 5-3 5S0 5 0 3a3 3 0 0 1 3-3z" fill="#d4b062"/></svg>Straßennamen, Nummer</div>
<div class="abs data-row" style="top:488px"><svg width="7" height="7" viewBox="0 0 7 7"><path d="M1 0.5l1.4 1.6-.7 1c.5 1 1.2 1.7 2.2 2.2l1-.7L6.5 6 5.6 6.8C3 6.5.5 4 .2 1.4z" fill="#d4b062"/></svg>Telefonnummer</div>
<div class="abs data-row" style="top:513px"><span style="color:#d4b062;font-size:8px">@</span>Email-Adresse</div>

<!-- sidebar: Öffnungszeiten -->
<div class="abs side-box" style="top:563px;height:172px">
  <div class="side-head">Öffnungszeiten<svg width="11" height="11" viewBox="0 0 11 11"><circle cx="5.5" cy="5.5" r="4.8" fill="none" stroke="#fff" stroke-width="1.1"/><path d="M5.5 2.8v2.9l1.8 1.1" fill="none" stroke="#fff" stroke-width="1.1"/></svg></div>
</div>
<div class="abs hours-row" style="top:588px"><span>Montag</span><span>8:00 bis 17:00 Uhr</span></div>
<div class="abs hours-row" style="top:612.5px"><span>Montag</span><span>8:00 bis 17:00 Uhr</span></div>
<div class="abs hours-row" style="top:637px"><span>Montag</span><span>8:00 bis 17:00 Uhr</span></div>
<div class="abs hours-row" style="top:661.5px"><span>Montag</span><span>8:00 bis 17:00 Uhr</span></div>
<div class="abs hours-row" style="top:686px"><span>Montag</span><span>8:00 bis 17:00 Uhr</span></div>
<div class="abs hours-row" style="top:710.5px"><span>Montag</span><span>8:00 bis 17:00 Uhr</span></div>

<!-- sidebar: Anfrage -->
<div class="abs side-box" style="top:761px;height:215px">
  <div class="side-head">Anfrage stellen</div>
</div>
<div class="abs field" style="top:799px;height:25px">Vor- und Nachname<svg width="8" height="8" viewBox="0 0 11 11"><circle cx="5.5" cy="5.5" r="5.5" fill="#d4b062"/><circle cx="5.5" cy="4.2" r="1.8" fill="#fff"/><path d="M2.5 9c.6-1.6 1.7-2.3 3-2.3s2.4.7 3 2.3z" fill="#fff"/></svg></div>
<div class="abs field" style="top:833px;height:24px">Email Adresse<span style="color:#d4b062;font-size:8px">@</span></div>
<div class="abs field" style="top:866px;height:60px;align-items:flex-start;padding-top:11px">Nachricht..</div>
<div class="abs btn-send">ANFRAGE SENDEN</div>

<footer class="abs site-footer"></footer>
<div class="abs footer-brand"><div class="ring"></div>Wir-bauen-Brücken</div>
<div class="abs footer-title" style="left:240px">Wir bauen Brücken</div>
<p class="abs footer-about">Duis sed odio sit amet nibh vulputate cursus a sit amet mauris. Morbi accumsan ipsum velit. Nam nec tellus a<a>Über uns</a></p>
<div class="abs footer-title" style="left:432px">WEBSITE</div>
<ul class="abs footer-links" style="left:432px"><li>Wir bauen Brücken</li><li>Unternehmen suchen</li><li>Mitgliedschaft</li><li>Kontakt</li></ul>
<div class="abs footer-title" style="left:560px">RECHTLICHES</div>
<ul class="abs footer-links" style="left:560px"><li>Impressum</li><li>Datenschutz</li><li>AGB</li><li>Sicherheitsbestimmungen</li></ul>
<div class="abs copyright">© 2020 Wir Bauen Brücken</div>

</body>
</html>
```